Washing powder bag design.

Project Description – Graphic Design Proposal for ORNE Laundry Powder Packaging
We have already explored initial design ideas internally, supported by AI-assisted tools (ChatGPT) to develop early concepts, layouts, and mockups. To support this, we have attached the bag die-cut, where graphics and text are placed as a visual guideline for the intended structure. In addition, we have included a mockup of the product series currently under development to clearly communicate the desired style, direction, and overall visual identity.
The mockup should be regarded as the design foundation for this project and as a starting point for professional refinement.
Scope of Work
We would like you to create three graphic design variants, each based on a different color direction:
1. Variant 1: In line with our current color scheme
2. Variant 2: A blue version
3. Variant 3: A green version
Design Elements to Be Preserved
The following elements must be maintained across all three variants:
• The overall style and visual expression of the mockup
• The leaf-shaped element in the bottom right corner
• The ORNE layout, including typography, positioning, and general look & feel
Summary
While the color palette may vary, the structure, style, and key design elements must remain consistent and be directly based on the attached mockup.
We look forward to seeing your creative interpretation and professional input.
Updates
We need the design to be created based on the attached die-cut file “Orne 10 kg BAG 202526”, including all text elements.
We would like the final to include both the designed die-cut file and a mockup.

```html
<!DOCTYPE html>
<html lang="da">
<head>
<meta charset="utf-8">
<title>ORNE Vaskepulver 10 kg – three colour variants</title>
<link href="https://fonts.googleapis.com/css2?family=Roboto+Condensed:wght@400;500;700&family=Open+Sans:wght@400;600;700&display=swap" rel="stylesheet">
<style>
  :root{
    --ink:#4b5a2f;
    --ink-soft:#5d6a44;
    --paper:#f4eedc;
    --hole:#ffffff;
    --hazard:#e0572d;
    --cream-bag:#efe3c2;
    --cream-edge:#e3d4ab;
    --cream-leaf:#c9d3a6;
    --blue-bag:#92d0d6;
    --blue-edge:#7fc2c9;
    --blue-leaf:#5fbcbc;
    --green-bag:#86dc5e;
    --green-edge:#72cf48;
    --green-leaf:#55bd35;
  }
  *{box-sizing:border-box;margin:0;padding:0}
  html,body{width:1200px;height:1197px;overflow:hidden;background:#fff}
  body{position:relative;font-family:"Roboto Condensed",Arial,sans-serif;color:var(--ink)}

  .tone-cream{--bag:var(--cream-bag);--edge:var(--cream-edge);--leaf:var(--cream-leaf)}
  .tone-blue{--bag:var(--blue-bag);--edge:var(--blue-edge);--leaf:var(--blue-leaf)}
  .tone-green{--bag:var(--green-bag);--edge:var(--green-edge);--leaf:var(--green-leaf)}

  .bag{position:absolute;width:222px;height:442px;background:linear-gradient(90deg,var(--edge) 0,var(--bag) 8%,var(--bag) 92%,var(--edge) 100%);border-radius:4px 4px 6px 6px;overflow:hidden}
  .bag::before{content:"";position:absolute;left:0;right:0;top:0;height:16px;background:repeating-linear-gradient(90deg,rgba(0,0,0,.06) 0 1px,transparent 1px 4px)}
  .holes{position:absolute;top:28px;left:0;right:0;display:flex;justify-content:center;gap:18px}
  .holes span{width:13px;height:13px;border-radius:50%;background:var(--hole)}

  /* front */
  .brand-name{position:absolute;left:0;right:0;top:152px;text-align:center;font-family:"Roboto Condensed",sans-serif;font-weight:700;font-size:40px;line-height:48px;letter-spacing:1px;color:var(--ink)}
  .product{position:absolute;left:0;right:0;top:246px;text-align:center;font-size:25px;line-height:30px;font-weight:700;letter-spacing:.3px;color:var(--ink)}
  .product-sub{position:absolute;left:0;right:0;top:276px;text-align:center;font-size:13.5px;line-height:16px;font-weight:500;color:var(--ink)}
  .tagline{position:absolute;left:0;right:0;top:302px;text-align:center;font-size:13px;line-height:16px;font-weight:500;color:var(--ink-soft)}
  .leaf-corner{position:absolute;right:-8px;bottom:10px;width:96px;height:150px;border-radius:80% 10% 70% 20%;background:linear-gradient(160deg,var(--leaf),transparent 85%);opacity:.75}
  .care-row{position:absolute;display:flex;align-items:center;gap:5px}
  .front .care-row{left:24px;top:366px}
  .care-icon{width:28px;height:28px;border:2.5px solid var(--ink);border-radius:5px;background:var(--paper);display:flex;align-items:center;justify-content:center;font-weight:700;font-size:11px;color:var(--ink)}
  .care-icon svg{width:18px;height:18px}
  .weight{font-size:16px;font-weight:700;margin-left:6px}
  .temps{position:absolute;font-weight:500;color:var(--ink);white-space:nowrap}
  .front .temps{left:24px;top:402px;font-size:10.5px}

  /* back */
  .usage{position:absolute;left:24px;top:78px;width:93px;height:352px;background:var(--paper);border:.5px solid #cfc5a6;padding:5px;font-family:"Open Sans",sans-serif;font-size:4.1px;line-height:5.3px;color:#555;overflow:hidden}
  .usage p{margin-bottom:4px}
  .usage b{color:#333}
  .warning{position:absolute;left:118px;top:78px;width:96px;height:160px;background:var(--paper);border:.5px solid #cfc5a6;padding:5px;font-family:"Open Sans",sans-serif;font-size:3.9px;line-height:5px;color:#555}
  .warning h3{font-size:5.8px;line-height:7px;text-align:center;color:#333;font-weight:700}
  .warning svg{display:block;width:36px;height:36px;margin:5px auto 8px}
  .warning p{margin-bottom:3px}
  .dosage{position:absolute;left:118px;top:242px;width:96px;height:140px;background:var(--paper);padding:6px 4px;text-align:center}
  .dosage h3{font-size:10px;line-height:10px;font-weight:500;color:var(--ink)}
  .dosage table{margin:5px auto 0;border-collapse:collapse;font-size:5.2px;color:#444}
  .dosage td,.dosage th{border:.5px solid #9a9a8a;padding:2px;font-weight:400;line-height:6px}
  .dosage th{font-size:4.8px}
  .dosage td.kg{font-size:6px;border-left:none}
  .dosage .note{font-size:5px;margin-top:3px;color:#444}
  .back .care-row{left:121px;top:388px;gap:4px}
  .back .care-icon{width:22px;height:22px;border-width:2px;font-size:8.5px}
  .back .care-icon svg{width:14px;height:14px}
  .back .temps{left:121px;top:416px;font-size:7px}
  .maker{position:absolute;left:2px;top:320px;width:20px;height:110px;background:var(--paper)}
  .maker span{position:absolute;left:50%;top:50%;transform:translate(-50%,-50%) rotate(90deg);white-space:nowrap;font-family:"Open Sans",sans-serif;font-size:3.8px;line-height:4.6px;color:#333}
  .maker strong{font-family:"Roboto Condensed",sans-serif;font-size:6px;line-height:7px;font-weight:700}
</style>
</head>
<body>

<!-- ===== cream variant ===== -->
<section class="bag front tone-cream" style="left:364px;top:130px">
  <div class="holes"><span></span><span></span><span></span></div>
  <p class="brand-name">ORNE</p>
  <h1 class="product">VASKEPULVER</h1>
  <p class="product-sub">LAUNDRY DETERGENT</p>
  <p class="tagline">RENT OG ROLIGT<br>I HVERDAGEN</p>
  <div class="leaf-corner" role="img" aria-label="Leaf sprig illustration in the bottom right corner"></div>
  <div class="care-row">
    <span class="care-icon">120</span>
    <span class="care-icon"><svg viewBox="0 0 18 18"><rect x="2" y="1.5" width="14" height="15" rx="1.5" fill="none" stroke="currentColor" stroke-width="1.6"/><circle cx="9" cy="10" r="4" fill="none" stroke="currentColor" stroke-width="1.6"/></svg></span>
    <span class="care-icon"><svg viewBox="0 0 18 18"><path d="M2 8h14l-2 8H4z" fill="none" stroke="currentColor" stroke-width="1.6"/><path d="M7 8V3l3 2" fill="none" stroke="currentColor" stroke-width="1.4"/></svg></span>
    <span class="weight">10kg</span>
  </div>
  <p class="temps">20°C| 30°C| 40°C| 60°C| 90°C</p>
</section>

<section class="bag back tone-cream" style="left:624px;top:34px">
  <div class="holes"><span></span><span></span><span></span></div>
  <div class="usage">
    <p><b>(DK) BRUGSANVISNING – ORNE VASKEPULVER</b></p>
    <p>Universel vaskepulver til alle vaskbare tekstiler fra 20 °C til 90 °C.</p>
    <p>Sorter tøjet efter farve. Dosér efter vandets hårdhed og snavsgrad.</p>
    <p>Opbevares tørt og lukket. Utilgængeligt for børn.</p>
    <p>Ingredienser: anioniske tensider, zeolitter, enzymer, parfume.</p>
    <p><b>(GB) USER GUIDE – ORNE LAUNDRY DETERGENT</b></p>
    <p>Universal detergent for all washable textiles from 20 °C to 90 °C.</p>
    <p>Sort laundry by colour. Dose according to water hardness and soil level.</p>
    <p>Store dry with the bag closed. Keep out of reach of children.</p>
    <p>Ingredients: anionic surfactants, zeolites, enzymes, perfume.</p>
  </div>
  <div class="warning">
    <h3>Advarsel<br>Warning</h3>
    <svg viewBox="0 0 40 40"><rect x="8" y="8" width="24" height="24" transform="rotate(45 20 20)" fill="#fff" stroke="var(--hazard)" stroke-width="2.5"/><rect x="18.6" y="11" width="2.8" height="12" rx="1" fill="#222"/><circle cx="20" cy="27.5" r="1.8" fill="#222"/></svg>
    <p><b>(DK)</b> Forårsager alvorlig øjenirritation. Kan udløse allergisk reaktion.</p>
    <p><b>(GB)</b> Causes serious eye irritation. May produce an allergic reaction.</p>
    <p>UFI: K2R7-0M4P-Q81T-ZX3W</p>
  </div>
  <div class="dosage">
    <h3>DOSERING<br>• DOSAGE</h3>
    <table>
      <tr><th></th><th>blød -<br>soft</th><th>medium</th><th>hård<br>- hard</th></tr>
      <tr><td class="kg">1 Kg</td><td>37 ml<br>≈ 41 g</td><td>37 ml<br>≈ 61 g</td><td>83 g</td></tr>
      <tr><td class="kg">5 Kg</td><td>75 Kg</td><td>75 ml<br>≈ 83 g</td><td>83 g</td></tr>
      <tr><td class="kg">10 Kg</td><td>112 Kg</td><td>112 ml<br>≈ 124 g</td><td>144 g</td></tr>
    </table>
    <p class="note">75 ml = 83 g</p>
  </div>
  <div class="care-row">
    <span class="care-icon">120</span>
    <span class="care-icon"><svg viewBox="0 0 18 18"><rect x="2" y="1.5" width="14" height="15" rx="1.5" fill="none" stroke="currentColor" stroke-width="1.6"/><circle cx="9" cy="10" r="4" fill="none" stroke="currentColor" stroke-width="1.6"/></svg></span>
    <span class="care-icon"><svg viewBox="0 0 18 18"><path d="M2 8h14l-2 8H4z" fill="none" stroke="currentColor" stroke-width="1.6"/><path d="M7 8V3l3 2" fill="none" stroke="currentColor" stroke-width="1.4"/></svg></span>
  </div>
  <p class="temps">20°C | 30°C | 40°C | 60°C | 90°C</p>
  <div class="maker"><span>Produceret i EU for <strong>KLARHUS</strong><br>Lærkevej 7, 6190 Solvig<br>www.klarhus.dk · 10 kg</span></div>
</section>

<!-- ===== blue variant ===== -->
<section class="bag front tone-blue" style="left:64px;top:730px">
  <div class="holes"><span></span><span></span><span></span></div>
  <p class="brand-name">ORNE</p>
  <h1 class="product">VASKEPULVER</h1>
  <p class="product-sub">LAUNDRY DETERGENT</p>
  <p class="tagline">RENT OG ROLIGT<br>I HVERDAGEN</p>
  <div class="leaf-corner" role="img" aria-label="Leaf sprig illustration in the bottom right corner"></div>
  <div class="care-row">
    <span class="care-icon">120</span>
    <span class="care-icon"><svg viewBox="0 0 18 18"><rect x="2" y="1.5" width="14" height="15" rx="1.5" fill="none" stroke="currentColor" stroke-width="1.6"/><circle cx="9" cy="10" r="4" fill="none" stroke="currentColor" stroke-width="1.6"/></svg></span>
    <span class="care-icon"><svg viewBox="0 0 18 18"><path d="M2 8h14l-2 8H4z" fill="none" stroke="currentColor" stroke-width="1.6"/><path d="M7 8V3l3 2" fill="none" stroke="currentColor" stroke-width="1.4"/></svg></span>
    <span class="weight">10kg</span>
  </div>
  <p class="temps">20°C| 30°C| 40°C| 60°C| 90°C</p>
</section>

<section class="bag back tone-blue" style="left:324px;top:634px">
  <div class="holes"><span></span><span></span><span></span></div>
  <div class="usage">
    <p><b>(DK) BRUGSANVISNING – ORNE VASKEPULVER</b></p>
    <p>Universel vaskepulver til alle vaskbare tekstiler fra 20 °C til 90 °C.</p>
    <p>Sorter tøjet efter farve. Dosér efter vandets hårdhed og snavsgrad.</p>
    <p>Opbevares tørt og lukket. Utilgængeligt for børn.</p>
    <p>Ingredienser: anioniske tensider, zeolitter, enzymer, parfume.</p>
    <p><b>(GB) USER GUIDE – ORNE LAUNDRY DETERGENT</b></p>
    <p>Universal detergent for all washable textiles from 20 °C to 90 °C.</p>
    <p>Sort laundry by colour. Dose according to water hardness and soil level.</p>
    <p>Store dry with the bag closed. Keep out of reach of children.</p>
    <p>Ingredients: anionic surfactants, zeolites, enzymes, perfume.</p>
  </div>
  <div class="warning">
    <h3>Advarsel<br>Warning</h3>
    <svg viewBox="0 0 40 40"><rect x="8" y="8" width="24" height="24" transform="rotate(45 20 20)" fill="#fff" stroke="var(--hazard)" stroke-width="2.5"/><rect x="18.6" y="11" width="2.8" height="12" rx="1" fill="#222"/><circle cx="20" cy="27.5" r="1.8" fill="#222"/></svg>
    <p><b>(DK)</b> Forårsager alvorlig øjenirritation. Kan udløse allergisk reaktion.</p>
    <p><b>(GB)</b> Causes serious eye irritation. May produce an allergic reaction.</p>
    <p>UFI: K2R7-0M4P-Q81T-ZX3W</p>
  </div>
  <div class="dosage">
    <h3>DOSERING<br>• DOSAGE</h3>
    <table>
      <tr><th></th><th>blød -<br>soft</th><th>medium</th><th>hård<br>- hard</th></tr>
      <tr><td class="kg">1 Kg</td><td>37 ml<br>≈ 41 g</td><td>37 ml<br>≈ 61 g</td><td>83 g</td></tr>
      <tr><td class="kg">5 Kg</td><td>75 Kg</td><td>75 ml<br>≈ 83 g</td><td>83 g</td></tr>
      <tr><td class="kg">10 Kg</td><td>112 Kg</td><td>112 ml<br>≈ 124 g</td><td>144 g</td></tr>
    </table>
    <p class="note">75 ml = 83 g</p>
  </div>
  <div class="care-row">
    <span class="care-icon">120</span>
    <span class="care-icon"><svg viewBox="0 0 18 18"><rect x="2" y="1.5" width="14" height="15" rx="1.5" fill="none" stroke="currentColor" stroke-width="1.6"/><circle cx="9" cy="10" r="4" fill="none" stroke="currentColor" stroke-width="1.6"/></svg></span>
    <span class="care-icon"><svg viewBox="0 0 18 18"><path d="M2 8h14l-2 8H4z" fill="none" stroke="currentColor" stroke-width="1.6"/><path d="M7 8V3l3 2" fill="none" stroke="currentColor" stroke-width="1.4"/></svg></span>
  </div>
  <p class="temps">20°C | 30°C | 40°C | 60°C | 90°C</p>
  <div class="maker"><span>Produceret i EU for <strong>KLARHUS</strong><br>Lærkevej 7, 6190 Solvig<br>www.klarhus.dk · 10 kg</span></div>
</section>

<!-- ===== green variant ===== -->
<section class="bag front tone-green" style="left:664px;top:730px">
  <div class="holes"><span></span><span></span><span></span></div>
  <p class="brand-name">ORNE</p>
  <h1 class="product">VASKEPULVER</h1>
  <p class="product-sub">LAUNDRY DETERGENT</p>
  <p class="tagline">RENT OG ROLIGT<br>I HVERDAGEN</p>
  <div class="leaf-corner" role="img" aria-label="Leaf sprig illustration in the bottom right corner"></div>
  <div class="care-row">
    <span class="care-icon">120</span>
    <span class="care-icon"><svg viewBox="0 0 18 18"><rect x="2" y="1.5" width="14" height="15" rx="1.5" fill="none" stroke="currentColor" stroke-width="1.6"/><circle cx="9" cy="10" r="4" fill="none" stroke="currentColor" stroke-width="1.6"/></svg></span>
    <span class="care-icon"><svg viewBox="0 0 18 18"><path d="M2 8h14l-2 8H4z" fill="none" stroke="currentColor" stroke-width="1.6"/><path d="M7 8V3l3 2" fill="none" stroke="currentColor" stroke-width="1.4"/></svg></span>
    <span class="weight">10kg</span>
  </div>
  <p class="temps">20°C| 30°C| 40°C| 60°C| 90°C</p>
</section>

<section class="bag back tone-green" style="left:922px;top:634px">
  <div class="holes"><span></span><span></span><span></span></div>
  <div class="usage">
    <p><b>(DK) BRUGSANVISNING – ORNE VASKEPULVER</b></p>
    <p>Universel vaskepulver til alle vaskbare tekstiler fra 20 °C til 90 °C.</p>
    <p>Sorter tøjet efter farve. Dosér efter vandets hårdhed og snavsgrad.</p>
    <p>Opbevares tørt og lukket. Utilgængeligt for børn.</p>
    <p>Ingredienser: anioniske tensider, zeolitter, enzymer, parfume.</p>
    <p><b>(GB) USER GUIDE – ORNE LAUNDRY DETERGENT</b></p>
    <p>Universal detergent for all washable textiles from 20 °C to 90 °C.</p>
    <p>Sort laundry by colour. Dose according to water hardness and soil level.</p>
    <p>Store dry with the bag closed. Keep out of reach of children.</p>
    <p>Ingredients: anionic surfactants, zeolites, enzymes, perfume.</p>
  </div>
  <div class="warning">
    <h3>Advarsel<br>Warning</h3>
    <svg viewBox="0 0 40 40"><rect x="8" y="8" width="24" height="24" transform="rotate(45 20 20)" fill="#fff" stroke="var(--hazard)" stroke-width="2.5"/><rect x="18.6" y="11" width="2.8" height="12" rx="1" fill="#222"/><circle cx="20" cy="27.5" r="1.8" fill="#222"/></svg>
    <p><b>(DK)</b> Forårsager alvorlig øjenirritation. Kan udløse allergisk reaktion.</p>
    <p><b>(GB)</b> Causes serious eye irritation. May produce an allergic reaction.</p>
    <p>UFI: K2R7-0M4P-Q81T-ZX3W</p>
  </div>
  <div class="dosage">
    <h3>DOSERING<br>• DOSAGE</h3>
    <table>
      <tr><th></th><th>blød -<br>soft</th><th>medium</th><th>hård<br>- hard</th></tr>
      <tr><td class="kg">1 Kg</td><td>37 ml<br>≈ 41 g</td><td>37 ml<br>≈ 61 g</td><td>83 g</td></tr>
      <tr><td class="kg">5 Kg</td><td>75 Kg</td><td>75 ml<br>≈ 83 g</td><td>83 g</td></tr>
      <tr><td class="kg">10 Kg</td><td>112 Kg</td><td>112 ml<br>≈ 124 g</td><td>144 g</td></tr>
    </table>
    <p class="note">75 ml = 83 g</p>
  </div>
  <div class="care-row">
    <span class="care-icon">120</span>
    <span class="care-icon"><svg viewBox="0 0 18 18"><rect x="2" y="1.5" width="14" height="15" rx="1.5" fill="none" stroke="currentColor" stroke-width="1.6"/><circle cx="9" cy="10" r="4" fill="none" stroke="currentColor" stroke-width="1.6"/></svg></span>
    <span class="care-icon"><svg viewBox="0 0 18 18"><path d="M2 8h14l-2 8H4z" fill="none" stroke="currentColor" stroke-width="1.6"/><path d="M7 8V3l3 2" fill="none" stroke="currentColor" stroke-width="1.4"/></svg></span>
  </div>
  <p class="temps">20°C | 30°C | 40°C | 60°C | 90°C</p>
  <div class="maker"><span>Produceret i EU for <strong>KLARHUS</strong><br>Lærkevej 7, 6190 Solvig<br>www.klarhus.dk · 10 kg</span></div>
</section>

</body>
</html>
```